Jewelers Website

This is for the DESIGN ONLY.
I am a software programmer and will be doing the development.
New website design for
www.lunacrestgems.com.au
Need a fresh new look for an online only jewellery business who produce their jewellery by hand. I would like it designed in a parallax style. Feel free to recommend fonts to use for the site. This is an Australian based company located in NSW so shots of sites in NSW might make nice background images.
http://vornaplex.me/demo/#theme=parallax
To contain the below sections
About Us
Contact Us
Gallery
Testimonials
Diamond Types
The colour scheme is to be Black / White and Silver.
With the Parallax style there will be moving sections and images for added impact.
Target Market(s)
Young Adults mainly engagement jewellery

```html
<!DOCTYPE html>
<html lang="en">
<head>
<meta charset="utf-8">
<title>Lunacrest Gems — Diamond engagement rings Australia</title>
<link href="https://fonts.googleapis.com/css2?family=Lato:wght@300;400;700;900&family=Oswald:wght@400;500&family=Open+Sans:ital,wght@0,400;0,600;0,700;1,700&family=Kaushan+Script&family=Josefin+Sans:wght@300;700&display=swap" rel="stylesheet">
<style>
:root{
  --black:#000;
  --ink:#1b1b1b;
  --nav:#262626;
  --white:#fff;
  --paper:#fff;
  --mist:#e4e4e4;
  --text:#3a3a3a;
  --yellow:#e5d300;
  --blue:#2e8fd6;
  --footer:#111;
}
*{box-sizing:border-box;margin:0;padding:0}
html,body{width:1200px;height:3536px;overflow:hidden}
body{position:relative;background:var(--black);font-family:"Open Sans",Arial,sans-serif;color:var(--text)}
section,header,nav,footer{position:absolute;left:0;width:1200px;overflow:hidden}
.abs{position:absolute}
.heading{font-family:"Oswald",Arial,sans-serif;font-weight:400;font-size:30px;text-align:center;width:100%;text-transform:uppercase;letter-spacing:.5px}

/* hero */
.hero{top:0;height:688px}
.hero-photo{position:absolute;inset:0;background:
  radial-gradient(ellipse 420px 200px at 760px 470px,rgba(240,235,220,.55),transparent 70%),
  radial-gradient(ellipse 900px 160px at 600px 560px,rgba(180,140,70,.35),transparent 70%),
  linear-gradient(180deg,#111418 0%,#1c232c 35%,#2a2a26 60%,#0e1216 100%)}
.hero-title{top:168px;width:100%;text-align:center;font-family:"Lato",Arial,sans-serif;color:var(--white);line-height:1.1}
.hero-title .first{display:inline-block;background:rgba(0,0,0,.55);padding:2px 28px;font-weight:900;font-size:54px}
.hero-title .second{display:block;font-weight:300;font-size:54px}
.hero-title .second b{font-weight:900}
.hero-sub{top:306px;width:100%;text-align:center;color:var(--white);font-style:italic;font-weight:700;font-size:14px;line-height:22px}
.hero-btn{left:573px;top:386px;width:118px;height:34px;background:var(--yellow);color:#222;font:700 12px "Open Sans",sans-serif;text-align:center;line-height:34px;letter-spacing:.5px}
.hero-down{left:609px;top:466px}
.hero-arrow{top:326px}

/* nav */
.site-nav{top:688px;height:78px;background:var(--nav)}
.brand{left:101px;top:20px;color:var(--white);font-family:"Lato",serif;font-size:19px;line-height:19px;letter-spacing:1px;text-transform:uppercase}
.menu{top:0;height:78px;display:flex;align-items:center;left:504px}
.menu a{color:var(--white);text-decoration:none;font-weight:700;font-size:13px;margin-right:40px}

/* about */
.about{top:766px;height:429px;background:var(--paper)}
.about .heading{top:62px;color:#111}
.about-tag{top:118px;width:100%;text-align:center;font-family:"Kaushan Script",cursive;font-size:17px;color:#111}
.about-copy{left:104px;top:162px;width:994px;text-align:center;font-size:12.5px;line-height:21px;color:#444}
.stat{top:300px;display:flex;align-items:center;gap:12px}
.stat .num{font-family:"Kaushan Script",cursive;font-size:52px;line-height:1}
.stat .lbl{font-size:15px;line-height:18px}
.stat.blue .num,.stat.blue .lbl{color:var(--blue)}
.stat.dark .num{color:#111;font-family:"Lato",sans-serif;font-weight:900;font-style:italic}
.stat.dark .lbl{color:#111}

/* help */
.help{top:1195px;height:412px;background:var(--black)}
.help-sparkle{right:0;top:0;width:380px;height:190px;background:radial-gradient(ellipse at 80% 20%,rgba(170,170,220,.45),transparent 65%)}
.help .heading{top:30px;color:var(--white)}
.guide{top:118px;width:240px;text-align:center;color:var(--white);font-size:15px;line-height:23px}
.guide .ring{width:156px;height:156px;border:4px solid var(--white);border-radius:50%;margin:0 auto 28px;display:flex;align-items:center;justify-content:center}
.guide.active{color:var(--yellow)}
.guide.active .ring{border-color:var(--yellow)}

/* gallery */
.gallery{top:1607px;height:585px;background:linear-gradient(180deg,#2a2f38 0%,#5b4d42 45%,#8a6a4c 60%,#2b3038 100%)}
.gallery .heading{top:40px;color:var(--white)}
.grid{left:99px;top:128px;width:1002px;display:grid;grid-template-columns:repeat(5,194px);grid-auto-rows:192px;gap:8px}
.tile{background:radial-gradient(circle at 50% 45%,#d9dde2 0%,#6b6f75 45%,#111 90%)}
.tile.dark{background:radial-gradient(circle at 50% 55%,#5a6a7a 0%,#151a20 45%,#000 85%)}
.tile.light{background:radial-gradient(circle at 50% 50%,#fff 0%,#c9cdd2 50%,#8a8e94 100%)}
.tile.ruby{background:radial-gradient(circle at 50% 60%,#c2334a 0%,#4a0f18 35%,#000 75%)}
.tile.caption{background:#000;color:var(--white);display:flex;flex-direction:column;align-items:center;justify-content:center;gap:18px;font-family:"Lato",serif;font-size:16px}
.tile.caption span{border:1.5px solid var(--white);border-radius:14px;padding:4px 12px;font-size:10px}
.side-arrow{top:300px}

/* testimonials */
.testimonials{top:2192px;height:325px;background:var(--mist)}
.testimonials .heading{top:40px;color:#111}
.quote-card{left:99px;top:123px;width:997px;height:117px;background:var(--white);text-align:center;font-size:10.5px;line-height:16px;color:#666;padding:22px 80px 0}
.quote-card .who{margin-top:22px;color:#333}
.qmark{font:900 42px/1 "Lato",serif;color:#111}
.dots{top:268px;width:100%;text-align:center}
.dots i{display:inline-block;width:9px;height:9px;border-radius:50%;background:#111;margin:0 4px}

/* diamond types */
.types{top:2517px;height:377px;background:linear-gradient(180deg,#0b0d12 0%,#1f2530 55%,#2d2a26 100%)}
.types .heading{top:66px;color:var(--white)}
.type{top:130px;width:240px;text-align:center;color:var(--white);font-size:15px;text-transform:uppercase}
.type .ring{width:130px;height:130px;border:2px solid rgba(255,255,255,.45);border-radius:50%;margin:0 auto 32px;display:flex;align-items:center;justify-content:center}
.type .stone{width:96px;height:96px;border-radius:50%;background:radial-gradient(circle,#fff 0%,#b9c9dc 50%,#6d7d92 100%)}
.type .stone.square{border-radius:4px;width:80px;height:80px}
.type .stone.marquise{width:56px;height:100px;border-radius:50%/50%}

/* contact */
.contact{top:2894px;height:554px;background:var(--ink);color:var(--white)}
.say{left:106px;top:52px;font-family:"Josefin Sans",sans-serif;font-size:64px;font-weight:300}
.say b{font-weight:700}
.contact-intro{left:106px;top:152px;width:490px;font-size:16px;line-height:27px}
.contact-row{display:flex;align-items:center;gap:18px;font-size:16px}
.divider{left:106px;top:305px;width:475px;height:1px;background:rgba(255,255,255,.5)}
.dot-icon{width:22px;height:22px;border-radius:50%;background:var(--white);flex:none}
.field{left:622px;width:486px;background:var(--white);border:1px solid #ccc;color:#999;font-size:14px;padding:12px 14px}

/* footer */
.site-footer{top:3448px;height:88px;background:var(--footer);color:var(--white);text-align:center;font-size:13px;line-height:88px}
</style>
</head>
<body>

<header class="hero">
  <div class="hero-photo" role="img" aria-label="Night view of Sydney harbour with the illuminated opera house and city skyline"></div>
  <svg class="abs hero-arrow" style="left:28px" width="66" height="58" viewBox="0 0 66 58"><rect width="66" height="58" fill="rgba(0,0,0,.35)"/><path d="M42 8 L18 29 L42 50" fill="none" stroke="#ddd" stroke-width="9"/></svg>
  <svg class="abs hero-arrow" style="left:1108px" width="66" height="58" viewBox="0 0 66 58"><rect width="66" height="58" fill="rgba(0,0,0,.35)"/><path d="M24 8 L48 29 L24 50" fill="none" stroke="#ddd" stroke-width="9"/></svg>
  <h1 class="abs hero-title"><span class="first">Diamond</span><span class="second">engagement rings <b>Australia</b></span></h1>
  <p class="abs hero-sub">Lorem ipsum dolor sit amet, consectetuer adipiscing elit, sed diam nonummy<br>nibh euismod tincidunt ut laoreet dolore magna aliquam erat volutpat.</p>
  <div class="abs hero-btn">LEARN MORE</div>
  <svg class="abs hero-down" width="44" height="44" viewBox="0 0 44 44"><circle cx="22" cy="22" r="21" fill="#fff"/><path d="M12 17 L22 27 L32 17" fill="none" stroke="#222" stroke-width="5"/></svg>
</header>

<nav class="site-nav">
  <div class="abs brand">Lunacrest<br>Gems</div>
  <div class="abs menu"><a>Home</a><a>About Us</a><a>Contact Us</a><a>Gallery</a><a>Testimonials</a><a>Diamond Types</a></div>
</nav>

<section class="about">
  <h2 class="abs heading">About Lunacrest Gems</h2>
  <p class="abs about-tag">what is it for?</p>
  <p class="abs about-copy">At Lunacrest Gems we are passionate about fine jewellery and gems. We feature one of a kind, original and elegant, handmade pieces. Lunacrest Gems handmade jewellery is crafted using exceptional quality metals, integrating designs that are innovative, creative, and unique.After you have consulted with our experienced staff - our highly trained and experienced jewellers hand-make every piece of finely crafted jewellery with a level of care and attention that cannot be matched by machines. Our custom jewellery is Australian-made in our Sydney workshop.With our combination of one-to-one customer service, our deep knowledge and experience, we can help you create unique jewellery that cannot be found in any jewellery store.</p>
  <div class="abs stat blue" style="left:313px"><span class="num">128</span><span class="lbl">happy<br>customers</span></div>
  <div class="abs stat dark" style="left:533px"><span class="num">345</span><span class="lbl">New<br>Products</span></div>
  <div class="abs stat blue" style="left:761px"><span class="num">8k</span><span class="lbl">social<br>followers</span></div>
</section>

<section class="help">
  <div class="abs help-sparkle" role="img" aria-label="Scattered sparkling diamonds on black"></div>
  <h2 class="abs heading">Help &amp; How To</h2>
  <div class="abs guide" style="left:69px"><div class="ring"><svg width="50" height="40" viewBox="0 0 50 40"><path d="M10 2 H40 L48 13 L25 38 L2 13 Z M2 13 H48 M18 2 L14 13 L25 38 L36 13 L32 2" fill="none" stroke="#fff" stroke-width="3"/></svg></div>Diamond Grading and<br>Quality</div>
  <div class="abs guide" style="left:344px"><div class="ring"><svg width="52" height="54" viewBox="0 0 52 54"><rect x="16" y="4" width="30" height="44" rx="3" fill="#fff"/><circle cx="12" cy="22" r="8" fill="#fff"/><path d="M6 30 L6 46 L12 41 L18 46 L18 30 Z" fill="#fff"/><path d="M24 20 H40 M24 28 H40 M24 36 H40" stroke="#000" stroke-width="2.5"/></svg></div>Diamond Certification</div>
  <div class="abs guide active" style="left:620px"><div class="ring"><svg width="30" height="50" viewBox="0 0 30 50"><text x="15" y="42" text-anchor="middle" font-family="Lato,sans-serif" font-weight="900" font-size="48" fill="#e5d300">?</text></svg></div>How To Choose A<br>Diamond</div>
  <div class="abs guide" style="left:898px"><div class="ring"><svg width="46" height="50" viewBox="0 0 46 50"><path d="M8 6 L24 26 L36 44 M38 6 L22 26 L10 44" fill="none" stroke="#fff" stroke-width="6" stroke-linecap="round"/></svg></div>Prince Cut Diamonds</div>
</section>

<section class="gallery" role="img" aria-label="Blurred city skyline at dusk behind the gallery">
  <h2 class="abs heading">Our Gallery</h2>
  <svg class="abs side-arrow" style="left:26px" width="20" height="36" viewBox="0 0 20 36"><path d="M16 2 L4 18 L16 34" fill="none" stroke="rgba(255,255,255,.6)" stroke-width="2"/></svg>
  <svg class="abs side-arrow" style="left:1152px" width="20" height="36" viewBox="0 0 20 36"><path d="M4 2 L16 18 L4 34" fill="none" stroke="rgba(255,255,255,.6)" stroke-width="2"/></svg>
  <div class="abs grid">
    <div class="tile" role="img" aria-label="Pile of loose diamonds"></div>
    <div class="tile caption">Lorem ipsum dolor<span>View large</span></div>
    <div class="tile dark" role="img" aria-label="Diamonds scattered on black"></div>
    <div class="tile light" role="img" aria-label="Close-up of a diamond on white"></div>
    <div class="tile light" role="img" aria-label="Several diamonds on a pale surface"></div>
    <div class="tile" role="img" aria-label="Cluster of diamonds on dark ground"></div>
    <div class="tile dark" role="img" aria-label="Single brilliant diamond with blue reflection"></div>
    <div class="tile dark" role="img" aria-label="Diamond necklace on black"></div>
    <div class="tile dark" role="img" aria-label="Blue gemstone on a dark surface"></div>
    <div class="tile ruby" role="img" aria-label="Red gemstones on black"></div>
  </div>
</section>

<section class="testimonials">
  <h2 class="abs heading">Testimonials</h2>
  <div class="abs quote-card">
    Etiam in tincidunt arcu, at tempor magna. Maecenas ut odio nunc. Fusce aliquet sem et sollicitudin tincidunt.<br>
    Aliquam convallis vitae metus ut luctus. Nulla vestibulum consequat sem, nec molestie tellus consectetur nec. In molestie sapien a convallis egestas.
    <p class="who">- John Doe, <b>developer</b></p>
  </div>
  <div class="abs qmark" style="left:122px;top:140px">&ldquo;</div>
  <div class="abs qmark" style="left:1048px;top:140px">&rdquo;</div>
  <div class="abs dots"><i></i><i></i><i></i></div>
</section>

<section class="types" role="img" aria-label="City skyline at night behind the diamond types">
  <h2 class="abs heading">Diamond Types</h2>
  <svg class="abs" style="left:20px;top:180px" width="20" height="36" viewBox="0 0 20 36"><path d="M16 2 L4 18 L16 34" fill="none" stroke="rgba(255,255,255,.5)" stroke-width="2"/></svg>
  <svg class="abs" style="left:1160px;top:180px" width="20" height="36" viewBox="0 0 20 36"><path d="M4 2 L16 18 L4 34" fill="none" stroke="rgba(255,255,255,.5)" stroke-width="2"/></svg>
  <div class="abs type" style="left:45px"><div class="ring"><div class="stone" role="img" aria-label="Round brilliant cut diamond"></div></div>Round Brilliant</div>
  <div class="abs type" style="left:340px"><div class="ring"><div class="stone" style="border-radius:30%" role="img" aria-label="Cushion cut diamond"></div></div>Cushion Cut</div>
  <div class="abs type" style="left:630px"><div class="ring"><div class="stone square" role="img" aria-label="Princess cut diamond"></div></div>Princess</div>
  <div class="abs type" style="left:920px"><div class="ring"><div class="stone marquise" role="img" aria-label="Marquise cut diamond"></div></div>Marquise</div>
</section>

<section class="contact">
  <h2 class="abs say">Say <b>Hello</b></h2>
  <p class="abs contact-intro">Don't be shy, drop us an email and say hello! We are a really nice bunch of people :)</p>
  <div class="abs contact-row" style="left:112px;top:248px"><svg width="18" height="28" viewBox="0 0 18 28"><rect x="1" y="1" width="16" height="26" rx="3" fill="#fff"/><rect x="4" y="5" width="10" height="15" fill="#1b1b1b"/></svg>(02) 5550 1472</div>
  <div class="abs contact-row" style="left:354px;top:248px"><svg width="26" height="18" viewBox="0 0 26 18"><rect width="26" height="18" fill="#fff"/><path d="M1 1 L13 10 L25 1" fill="none" stroke="#1b1b1b" stroke-width="2"/></svg>hello@lunacrestgems.com.au</div>
  <div class="abs divider"></div>
  <div class="abs contact-row" style="left:110px;top:342px"><span class="dot-icon"></span>@lunacrestgems</div>
  <div class="abs contact-row" style="left:354px;top:342px"><span class="dot-icon"></span>circlepage.com/lunacrest</div>
  <div class="abs contact-row" style="left:110px;top:410px"><span class="dot-icon"></span>orbitfeed.com/lunacrest</div>
  <div class="abs contact-row" style="left:354px;top:410px"><span class="dot-icon"></span>snapmural.com/lunacrest</div>
  <div class="abs field" style="top:66px;height:54px">Your Name *</div>
  <div class="abs field" style="top:151px;height:55px">Your E-mail *</div>
  <div class="abs field" style="top:226px;height:222px">Your Message *</div>
</section>

<footer class="site-footer">copyrights © 2014 lunacrestgems• all rights reserved</footer>

</body>
</html>
```